Website Revamp: Bravoly.com

Just got a new logo looking for a web design to go with the business. I need the photoshop files and stock photos. No Word Press Please.

```html
<!DOCTYPE html>
<html lang="en">
<head>
<meta charset="utf-8">
<title>Bravoly Auto Recycling</title>
<link href="https://fonts.googleapis.com/css2?family=Rubik:wght@400;500;700&family=Roboto:wght@400;500;700&display=swap" rel="stylesheet">
<style>
:root{
  --green:#6cbd2f;
  --green-dark:#5aa423;
  --charcoal:#545454;
  --text:#555555;
  --muted:#777777;
  --light:#f2f2f2;
  --white:#ffffff;
}
*{box-sizing:border-box;margin:0;padding:0}
html,body{width:1200px;height:3869px;overflow:hidden}
body{position:relative;font-family:'Roboto',sans-serif;color:var(--text);background:var(--white)}
.abs{position:absolute}
.heading{font-family:'Rubik',sans-serif;font-weight:500;color:#444;text-transform:uppercase;letter-spacing:-0.5px}
.heading span{color:var(--green)}
.btn{position:absolute;display:flex;align-items:center;justify-content:center;gap:10px;border-radius:30px;color:#fff;font-family:'Rubik',sans-serif;font-weight:500;font-size:17px;text-transform:uppercase}
.btn-green{background:var(--green)}
.btn-dark{background:var(--charcoal)}

/* header */
.topline{left:0;top:0;width:1200px;height:5px;background:var(--green)}
.search{left:110px;top:25px;width:245px;height:44px;border:1px solid #ddd;border-radius:24px;box-shadow:0 1px 3px rgba(0,0,0,.08);font-size:13px;color:#777;padding:15px 0 0 14px}
.search-btn{position:absolute;right:5px;top:5px;width:32px;height:32px;border-radius:50%;background:var(--green);display:flex;align-items:center;justify-content:center}
.call{left:896px;top:24px;display:flex;align-items:center;gap:10px}
.call-icon{width:42px;height:42px;border:2px solid var(--green);border-radius:50%;display:flex;align-items:center;justify-content:center}
.call small{display:block;font-size:14px;color:#555}
.call strong{display:block;font-size:21px;color:var(--green);font-weight:700;margin-top:1px}
.nav{left:0;top:84px;width:1200px;height:44px;background:var(--charcoal)}
.nav a{position:absolute;top:0;height:44px;line-height:44px;color:#fff;font-size:14.5px;font-weight:500;text-decoration:none;text-transform:uppercase}
.nav a.active{background:var(--green);padding:0 19px}
.logo-cap{left:478px;top:-83px;width:244px;height:248px;border-radius:50%;background:#fff}
.logo-ring{left:562px;top:20px;width:76px;height:76px;border:5px solid var(--green);border-radius:50%}
.logo-name{left:480px;top:100px;width:240px;text-align:center;font-family:'Rubik',sans-serif;font-weight:700;font-size:27px;color:var(--green)}

/* hero */
.hero{left:0;top:128px;width:1200px;height:563px;background:linear-gradient(180deg,#3f79c4 0%,#6fa0d6 22%,#8c8d8e 45%,#5a4c48 70%,#2d2826 100%)}
.hero-panel{left:335px;top:279px;width:530px;height:170px;background:rgba(60,60,60,.45)}
.hero-title{left:0;top:292px;width:1200px;text-align:center;font-family:'Rubik',sans-serif;font-weight:500;font-size:50px;color:#fff;letter-spacing:-1px}
.hero-text{left:340px;top:366px;width:520px;text-align:center;font-size:16.5px;line-height:26px;color:#fff;font-weight:500}
.hero-arrow{top:381px;width:42px;height:42px;border:2px solid #fff;border-radius:50%;display:flex;align-items:center;justify-content:center}

/* services */
.sec-title{left:0;width:1200px;text-align:center;font-size:35px}
.sec-text{left:190px;top:836px;width:820px;text-align:center;font-size:15.5px;line-height:24px;color:#555}
.svc{top:927px;width:344px;height:344px;border-radius:50%;background:var(--charcoal);color:#fff;text-align:center}
.svc.featured{background:var(--green);border:10px solid #fff;top:927px;width:364px;height:364px}
.svc .icon{position:absolute;left:50%;top:62px;transform:translateX(-50%)}
.svc h3{position:absolute;left:0;top:150px;width:100%;font-family:'Rubik',sans-serif;font-weight:500;font-size:19.5px}
.svc p{position:absolute;left:50px;top:189px;width:244px;font-size:14px;line-height:21.5px;color:#eee}
.svc .more{position:absolute;left:50%;top:280px;margin-left:-19px;width:38px;height:38px;border:2px solid #fff;border-radius:50%;display:flex;align-items:center;justify-content:center}
.svc.featured h3{top:140px}
.svc.featured p{top:179px}
.svc.featured .more{top:270px}
.svc.featured .icon{top:52px}

/* why */
.why-photo{left:0;top:1386px;width:601px;height:474px;background:linear-gradient(180deg,#4a86d0 0%,#9ec3ea 35%,#7a5d55 60%,#6a4040 80%,#4b3a33 100%)}
.why-panel{left:601px;top:1386px;width:599px;height:474px;background:var(--green)}
.why-title{left:650px;top:1420px;font-family:'Rubik',sans-serif;font-weight:500;font-size:35px;color:#fff}
.why-item{left:650px;width:450px;color:#fff}
.why-item .ring{position:absolute;left:0;top:6px;width:58px;height:58px;border:2px solid #fff;border-radius:50%;display:flex;align-items:center;justify-content:center}
.why-item h4{position:absolute;left:76px;top:0;font-family:'Rubik',sans-serif;font-weight:500;font-size:16.5px;white-space:nowrap}
.why-item p{position:absolute;left:77px;top:24px;width:370px;font-size:13px;line-height:21px}

/* about */
.about-text{left:111px;top:2052px;width:505px;font-size:15.5px;line-height:28.6px;text-align:justify;color:#555}
.about-photo{left:709px;top:1963px;width:370px;height:370px;border-radius:50%;background:radial-gradient(circle at 50% 45%,#d9e6d2 0%,#a6c595 45%,#5d8f55 75%,#3f6a3c 100%)}

/* news */
.news-bg{left:0;top:2436px;width:1200px;height:610px;background:var(--light)}
.card{top:2550px;width:309px;height:394px;background:#fff;box-shadow:0 2px 6px rgba(0,0,0,.08)}
.card .img{height:189px}
.card .meta{position:absolute;left:20px;top:206px;font-size:13px;color:#666;display:flex;gap:10px;align-items:center}
.card h3{position:absolute;left:20px;top:238px;width:275px;font-size:16.5px;line-height:23.5px;font-weight:500;color:#222}
.card p{position:absolute;left:20px;top:296px;width:270px;font-size:14px;line-height:22px;color:#666}
.card .foot{position:absolute;left:0;top:355px;width:100%;border-top:1px solid #eee;height:39px;padding:12px 20px 0;font-size:12.5px;color:#444;display:flex;justify-content:space-between}

/* contact */
.contact{left:0;top:3046px;width:1200px;height:454px;background:linear-gradient(180deg,#73c236 0%,#6ab52f 50%,#79c23c 100%)}
.contact-title{left:0;top:3086px;width:1200px;text-align:center;font-family:'Rubik',sans-serif;font-weight:500;font-size:35px;color:#fff}
.field{left:228px;width:361px;height:48px;border:2px solid #fff;border-radius:26px;color:#fff;font-size:13.5px;padding:14px 0 0 28px;display:flex;gap:8px}
.field.msg{left:610px;top:3163px;width:362px;height:169px;border-radius:22px;padding-top:18px}

/* footer */
.f-ring{left:157px;top:3598px;width:78px;height:78px;border:5px solid var(--green);border-radius:50%}
.f-name{left:112px;top:3678px;width:168px;text-align:center;font-family:'Rubik',sans-serif;font-weight:700;font-size:28px;color:var(--green)}
.social{top:3729px;width:34px;height:34px;border:2px solid #333;border-radius:50%}
.f-col h5{font-family:'Roboto',sans-serif;font-weight:500;font-size:17px;color:#222;margin-bottom:18px}
.f-col li{list-style:none;font-size:14px;color:#555;display:flex;gap:10px;align-items:flex-start;line-height:21px}
.f-rule{left:111px;top:3815px;width:978px;height:1px;background:#ddd}
.copy{left:0;top:3837px;width:1200px;text-align:center;font-size:14px;color:#555}
</style>
</head>
<body>

<!-- header -->
<div class="abs topline"></div>
<div class="abs search">Search
  <div class="search-btn"><svg width="14" height="14" viewBox="0 0 14 14"><circle cx="6" cy="6" r="4" fill="none" stroke="#fff" stroke-width="2"/><line x1="9" y1="9" x2="12.5" y2="12.5" stroke="#fff" stroke-width="2"/></svg></div>
</div>
<div class="abs call">
  <div class="call-icon"><svg width="20" height="20" viewBox="0 0 24 24"><path d="M6.6 10.8a15.1 15.1 0 0 0 6.6 6.6l2.2-2.2a1 1 0 0 1 1-.25 11.4 11.4 0 0 0 3.6.6 1 1 0 0 1 1 1V20a1 1 0 0 1-1 1A17 17 0 0 1 3 4a1 1 0 0 1 1-1h3.5a1 1 0 0 1 1 1c0 1.25.2 2.45.6 3.6a1 1 0 0 1-.25 1z" fill="#6cbd2f"/></svg></div>
  <div><small>Call Us:</small><strong>555-014-2398</strong></div>
</div>
<nav class="abs nav">
  <a class="active" style="left:91px">Home</a>
  <a style="left:201px">About Us</a>
  <a style="left:320px">Services</a>
  <a style="left:827px">Why Us</a>
  <a style="left:931px">News</a>
  <a style="left:1019px">Contact</a>
</nav>

<!-- hero -->
<div class="abs hero" role="img" aria-label="Photo of a large pile of scrapped cars under a blue sky"></div>
<div class="abs logo-cap"></div>
<div class="abs logo-ring"></div>
<div class="abs logo-name">BRAVOLY</div>
<div class="abs hero-panel"></div>
<div class="abs hero-title">BRAVOLY</div>
<div class="abs hero-text">Lorem ipsum dolor sit amet, consectetur adipiscing elit, sed do eiusmod tempor incididunt ut labore et dolore aliqua.</div>
<div class="btn btn-green" style="left:508px;top:449px;width:186px;height:50px">Get Started
  <svg width="16" height="16" viewBox="0 0 16 16"><circle cx="8" cy="8" r="8" fill="#fff"/><path d="M6 4.5 9.5 8 6 11.5" fill="none" stroke="#6cbd2f" stroke-width="2"/></svg></div>
<div class="abs hero-arrow" style="left:32px"><svg width="14" height="14" viewBox="0 0 14 14"><path d="M9 2 4 7l5 5" fill="none" stroke="#fff" stroke-width="2"/></svg></div>
<div class="abs hero-arrow" style="left:1128px"><svg width="14" height="14" viewBox="0 0 14 14"><path d="M5 2l5 5-5 5" fill="none" stroke="#fff" stroke-width="2"/></svg></div>

<!-- services -->
<h2 class="abs heading sec-title" style="top:782px">Our <span>Services</span></h2>
<p class="abs sec-text">Lorem ipsum dolor sit amet, consectetur adipiscing elit, sed do eiusmod tempor incididunt ut labore et dolore magna aliqua. Ut enim ad minim veniam, quis nostrud exercitation ullamco laboris nisi</p>

<div class="abs svc" style="left:106px">
  <svg class="icon" width="76" height="60" viewBox="0 0 76 60" fill="none" stroke="#fff" stroke-width="3"><rect x="4" y="6" width="42" height="36" rx="3"/><path d="M46 18h14l10 12v12H46z"/><circle cx="18" cy="46" r="7" fill="#545454"/><circle cx="58" cy="46" r="7" fill="#545454"/><path d="M18 20a8 8 0 0 1 14 0M32 28a8 8 0 0 1-14 0"/></svg>
  <h3>LOREM IPSUM DOLOR</h3>
  <p>Helmora is designing and developing head protection products to reduce the likelihood of concussion</p>
  <div class="more"><svg width="14" height="14" viewBox="0 0 14 14"><path d="M2 5l5 5 5-5" fill="none" stroke="#fff" stroke-width="2"/></svg></div>
</div>
<div class="abs svc" style="left:750px">
  <svg class="icon" width="84" height="60" viewBox="0 0 84 60" fill="none" stroke="#fff" stroke-width="3"><path d="M8 38l8-16h52l8 16v10H8z"/><circle cx="24" cy="48" r="7" fill="#545454"/><circle cx="60" cy="48" r="7" fill="#545454"/><path d="M20 4l8 8M64 4l-8 8M42 2v8"/></svg>
  <h3>LOREM IPSUM DOLOR</h3>
  <p>Soccer has no head protection product despite recent high profile head injuries, concern over</p>
  <div class="more"><svg width="14" height="14" viewBox="0 0 14 14"><path d="M2 5l5 5 5-5" fill="none" stroke="#fff" stroke-width="2"/></svg></div>
</div>
<div class="abs svc featured" style="left:416px">
  <svg class="icon" width="100" height="62" viewBox="0 0 100 62" fill="none" stroke="#fff" stroke-width="3"><path d="M4 22h20v28H4z"/><path d="M24 14h60v36H24z"/><path d="M34 22v22M46 22v22M58 22v22M70 22v22"/><circle cx="16" cy="52" r="7" fill="#6cbd2f"/><circle cx="76" cy="52" r="7" fill="#6cbd2f"/><path d="M86 8l8-6M88 16h8"/></svg>
  <h3>LOREM IPSUM DOLOR</h3>
  <p>Our initial product will be simplistic in function and design to ensure we get to market in 2020.</p>
  <div class="more"><svg width="14" height="14" viewBox="0 0 14 14"><path d="M2 5l5 5 5-5" fill="none" stroke="#fff" stroke-width="2"/></svg></div>
</div>

<!-- why choose us -->
<div class="abs why-photo" role="img" aria-label="Photo of stacked crushed cars against a cloudy blue sky"></div>
<div class="abs why-panel"></div>
<h2 class="abs why-title">WHY CHOOSE US?</h2>
<div class="abs why-item" style="top:1496px">
  <div class="ring"><svg width="32" height="20" viewBox="0 0 32 20" fill="none" stroke="#fff" stroke-width="1.6"><path d="M2 12l4-7h20l4 7v4H2z"/><circle cx="9" cy="16" r="2.5"/><circle cx="23" cy="16" r="2.5"/></svg></div>
  <h4>CAR COLLECTION</h4>
  <p>Lorem ipsum dolor sit amet, consectetur adipiscing elit, sed do eiusmod tempor incididunt</p>
</div>
<div class="abs why-item" style="top:1583px">
  <div class="ring"><svg width="32" height="22" viewBox="0 0 32 22" fill="none" stroke="#fff" stroke-width="1.6"><rect x="3" y="4" width="26" height="13" rx="2"/><circle cx="9" cy="18" r="2.5"/><circle cx="23" cy="18" r="2.5"/><path d="M12 8a4 4 0 0 1 8 0M20 12a4 4 0 0 1-8 0"/></svg></div>
  <h4>RESPONSIBLE RECYCLING</h4>
  <p>Lorem ipsum dolor sit amet, consectetur adipiscing elit, sed do eiusmod tempor incididunt</p>
</div>
<div class="abs why-item" style="top:1671px">
  <div class="ring"><svg width="28" height="26" viewBox="0 0 28 26" fill="none" stroke="#fff" stroke-width="1.6"><path d="M14 24C6 18 3 13 3 9a5 5 0 0 1 11-2 5 5 0 0 1 11 2c0 4-3 9-11 15z"/></svg></div>
  <h4>FRIENDLY SERVICE</h4>
  <p>Lorem ipsum dolor sit amet, consectetur adipiscing elit, sed do eiusmod tempor incididunt</p>
</div>
<div class="btn btn-dark" style="left:650px;top:1769px;width:169px;height:48px">Learn More
  <svg width="16" height="16" viewBox="0 0 16 16"><circle cx="8" cy="8" r="8" fill="#fff"/><path d="M6 4.5 9.5 8 6 11.5" fill="none" stroke="#545454" stroke-width="2"/></svg></div>

<!-- about -->
<h2 class="abs heading" style="left:111px;top:1988px;font-size:35px">About <span>Us</span></h2>
<p class="abs about-text">Lorem ipsum dolor sit amet, consectetur adipiscing elit, sed eiusmod tempor incididunt ut labore et dolore magna aliqua. Ut enim ad minim veniam, quis nostrud exercitation ullamco laboris nisi ut aliquip ex ea commodo consequat. Duis aute irure dolor in reprehenderit in voluptate velit esse cillum dolore eu fugiat nulla pariatur. Excepteur sint occaecat cupidatat non proident, sunt in culpa qui officia</p>
<div class="btn btn-green" style="left:111px;top:2253px;width:168px;height:48px">Learn More
  <svg width="16" height="16" viewBox="0 0 16 16"><circle cx="8" cy="8" r="8" fill="#fff"/><path d="M6 4.5 9.5 8 6 11.5" fill="none" stroke="#6cbd2f" stroke-width="2"/></svg></div>
<div class="abs about-photo" role="img" aria-label="Circular green collage of a recycling theme with scrapped vehicles"></div>

<!-- news -->
<div class="abs news-bg"></div>
<h2 class="abs heading sec-title" style="top:2482px">Latest <span>News</span></h2>

<article class="abs card" style="left:111px">
  <div class="img" role="img" aria-label="Photo of a pile of scrapped cars" style="background:linear-gradient(180deg,#5a95d8 0%,#bcd6ef 45%,#8a5a52 75%,#4a5a50 100%)"></div>
  <div class="meta"><span>By Admin</span><span>|</span><span>March 08, 2020</span></div>
  <h3>Lorem ipsum dolor sit consectetur adipiscing elit, sed do</h3>
  <p>Sed ut perspiciatis unde omnis natus sit voluptatem accusantium</p>
  <div class="foot"><span>0 Comment</span><svg width="14" height="12" viewBox="0 0 14 12"><path d="M8 1l5 4-5 4V7C4 7 2 8 1 11c0-4 2-7 7-7z" fill="#6cbd2f"/></svg></div>
</article>
<article class="abs card" style="left:445px">
  <div class="img" role="img" aria-label="Illustration of a leafy green car beside a recycling symbol on grass" style="background:linear-gradient(180deg,#8fc3ea 0%,#d6ebf6 45%,#7cbf3f 70%,#3f8a23 100%)"></div>
  <div class="meta"><span>By Admin</span><span>|</span><span>March 08, 2020</span></div>
  <h3>Lorem ipsum dolor sit consectetur adipiscing elit, sed do</h3>
  <p>Sed ut perspiciatis unde omnis natus sit voluptatem accusantium</p>
  <div class="foot"><span>0 Comment</span><svg width="14" height="12" viewBox="0 0 14 12"><path d="M8 1l5 4-5 4V7C4 7 2 8 1 11c0-4 2-7 7-7z" fill="#6cbd2f"/></svg></div>
</article>
<article class="abs card" style="left:779px">
  <div class="img" role="img" aria-label="Photo of compacted scrap metal bales" style="background:linear-gradient(180deg,#8a9bb0 0%,#6b6b6d 40%,#4a4a4c 75%,#3a3a3a 100%)"></div>
  <div class="meta"><span>By Admin</span><span>|</span><span>March 08, 2020</span></div>
  <h3>Lorem ipsum dolor sit consectetur adipiscing elit, sed do</h3>
  <p>Sed ut perspiciatis unde omnis natus sit voluptatem accusantium</p>
  <div class="foot"><span>0 Comment</span><svg width="14" height="12" viewBox="0 0 14 12"><path d="M8 1l5 4-5 4V7C4 7 2 8 1 11c0-4 2-7 7-7z" fill="#6cbd2f"/></svg></div>
</article>

<!-- contact -->
<div class="abs contact" role="img" aria-label="Green tinted photo of scrap metal"></div>
<h2 class="abs contact-title">CONTACT US</h2>
<div class="abs field" style="top:3163px">✎ Name</div>
<div class="abs field" style="top:3223px">✉ Email</div>
<div class="abs field" style="top:3283px">☏ Phone</div>
<div class="abs field msg">✉ Message</div>
<div class="btn btn-dark" style="left:520px;top:3375px;width:159px;height:46px;font-size:15px">Submit
  <svg width="14" height="14" viewBox="0 0 16 16"><circle cx="8" cy="8" r="8" fill="#fff"/><path d="M6 4.5 9.5 8 6 11.5" fill="none" stroke="#545454" stroke-width="2"/></svg></div>

<!-- footer -->
<div class="abs f-ring"></div>
<div class="abs f-name">BRAVOLY</div>
<div class="abs social" style="left:114px"></div>
<div class="abs social" style="left:154px"></div>
<div class="abs social" style="left:195px"></div>
<div class="abs social" style="left:235px"></div>

<div class="abs f-col" style="left:416px;top:3584px">
  <h5>Quick Links</h5>
  <ul style="display:flex;flex-direction:column;gap:11.5px">
    <li><span style="color:var(--green)">»</span>Home</li>
    <li><span style="color:var(--green)">»</span>About Us</li>
    <li><span style="color:var(--green)">»</span>Services</li>
    <li><span style="color:var(--green)">»</span>Why Us</li>
    <li><span style="color:var(--green)">»</span>Blog</li>
  </ul>
</div>
<div class="abs f-col" style="left:629px;top:3582px">
  <h5>Contact Us</h5>
  <ul style="display:flex;flex-direction:column;gap:11px">
    <li><span style="color:var(--green)">⚲</span>123, Lorem ipsum dolor amet<br>consectetur adipiscing</li>
    <li><span style="color:var(--green)">☏</span>+888 888 8888</li>
    <li><span style="color:var(--green)">▣</span>123 456 7890</li>
    <li><span style="color:var(--green)">✉</span>info@bravoly.com</li>
  </ul>
</div>
<div class="abs f-col" style="left:966px;top:3584px">
  <h5>Important</h5>
  <ul style="display:flex;flex-direction:column;gap:11.5px">
    <li><span style="color:var(--green)">»</span>Terms of Use</li>
    <li><span style="color:var(--green)">»</span>Site Map</li>
    <li><span style="color:var(--green)">»</span>Privacy Policy</li>
    <li><span style="color:var(--green)">»</span>Disclaimer</li>
  </ul>
</div>
<div class="abs f-rule"></div>
<div class="abs copy">© 2020 bravoly. All Rights Reserved</div>

</body>
</html>
```